Finiding oppertunites in Real Estate 6.15.20

size of ad 7” x 9.6”
1-I like the ad to stand out and attract people's attention.
2-you should be able to see the text of the ad clearly .. see the attachment anything in yellow is instructions.
3-the list of topics should not be the main part of the ad
4-if you decide you want a picture or vector of a person .. (you decide)
then it should be a white male about 25-30 years old wearing a solid white or blue shirt and not long hair.
5-leave 1 inch for footer
see attachment
Good luck

Target Market(s)

potential male students 25-35 years of age

Industry/Entity Type

Education

Requirements
Must have
• will stand out and people would want to see it.
should be able to read the words of ad
Nice to have
• how to make money in real estate on one line

```html
<!DOCTYPE html>
<html lang="en">
<head>
<meta charset="utf-8">
<title>Real Estate Course Flyer</title>
<link href="https://fonts.googleapis.com/css2?family=Red+Hat+Display:wght@400;500;700;800;900&family=Red+Hat+Text:wght@400;500&family=Archivo:ital,wght@0,700;1,800&display=swap" rel="stylesheet">
<style>
  :root {
    --stage: #5a5a5a;
    --paper: #f1f0ee;
    --gold: #9b7a3f;
    --gold-light: #e7dcc3;
    --gold-deep: #a58545;
    --navy: #0f2850;
    --red: #d0121b;
    --ink: #2a2a2a;
    --cream: #f7efdc;
  }
  * { margin: 0; padding: 0; box-sizing: border-box; }
  html, body { width: 1200px; height: 1200px; overflow: hidden; }
  body {
    background: var(--stage);
    display: flex; align-items: center; justify-content: center;
    font-family: "Red Hat Text", sans-serif;
  }
  .flyer {
    position: relative;
    width: 835px; height: 1180px;
    background: var(--paper);
    transform: scale(0.96);
    overflow: hidden;
  }
  .course-title {
    position: absolute; top: 78px; left: 0; width: 100%;
    text-align: center;
    font-family: "Red Hat Display", sans-serif; font-weight: 800;
    font-size: 52px; letter-spacing: 1px; color: var(--gold);
  }
  .headline-band {
    position: absolute; top: 160px; left: 0; width: 100%; height: 82px;
    background: linear-gradient(180deg, #d9c9a3 0%, #eee6d3 55%, var(--paper) 100%);
    display: flex; align-items: center; justify-content: center;
  }
  .headline {
    font-family: "Red Hat Display", sans-serif; font-weight: 800;
    font-size: 44px; color: var(--navy); margin-top: -6px;
  }
  .tagline {
    position: absolute; top: 258px; left: 0; width: 100%;
    text-align: center;
    font-family: "Red Hat Display", sans-serif; font-weight: 900;
    font-size: 38px; line-height: 44px; color: var(--red);
  }
  .houses-art {
    position: absolute; top: 390px; left: 0; width: 100%; height: 145px;
    background: radial-gradient(ellipse at 50% 55%, #ffffff 0%, #e4e4e4 55%, var(--paper) 100%);
  }
  .sessions-box {
    position: absolute; top: 542px; left: 103px; width: 630px; height: 211px;
    background: radial-gradient(ellipse at 50% 35%, #c6a868 0%, var(--gold-deep) 55%, #8e7038 100%);
  }
  .sessions-art {
    position: absolute; top: 20px; left: 187px; width: 240px; height: 100px;
    background: linear-gradient(90deg, #dfe7f0 0%, #f0a03a 45%, #2a3f6e 100%);
    border-radius: 3px;
  }
  .sessions-text {
    position: absolute; top: 112px; left: 0; width: 100%;
    text-align: center; color: var(--cream);
    font-family: "Archivo", sans-serif; font-weight: 700;
    font-size: 34px; line-height: 43px;
  }
  .topics-heading {
    position: absolute; top: 760px; left: 103px; width: 630px;
    display: flex; align-items: center; gap: 12px;
    font-family: "Red Hat Display", sans-serif; font-weight: 500;
    font-size: 24px; color: var(--navy);
  }
  .topics-heading::before, .topics-heading::after {
    content: ""; flex: 1; height: 1px; background: var(--gold);
  }
  .lower-band {
    position: absolute; top: 870px; left: 0; width: 100%; height: 177px;
    background: linear-gradient(180deg, var(--paper) 0%, #e9e0cb 50%, #d7c6a0 100%);
  }
  .topics {
    position: absolute; top: 795px; left: 103px; width: 640px;
    display: grid; grid-template-columns: 247px 243px 150px;
  }
  .topics ul { list-style: none; }
  .topics li {
    display: flex; align-items: center; gap: 12px;
    height: 25.8px; font-size: 15px; color: var(--ink);
  }
  .topics svg { width: 14px; height: 14px; flex: none; }
  .topics-rule {
    position: absolute; top: 937px; left: 103px; width: 630px; height: 1px;
    background: var(--gold);
  }
  .audience {
    position: absolute; top: 950px; left: 0; width: 100%;
    text-align: center; font-family: "Red Hat Display", sans-serif; font-weight: 400;
    font-size: 37px; line-height: 39px; color: var(--navy);
  }
  .footer {
    position: absolute; top: 1047px; left: 0; width: 100%; height: 133px;
    background: var(--paper);
  }
  .address {
    position: absolute; top: 38px; left: 48px;
    display: flex; align-items: center; gap: 12px;
    font-size: 15px; line-height: 18px; color: var(--ink);
  }
  .contacts {
    position: absolute; top: 24px; left: 332px; list-style: none;
  }
  .contacts li {
    display: flex; align-items: center; gap: 14px;
    height: 22.5px; font-size: 15px; color: var(--ink);
  }
  .contacts svg { width: 14px; height: 14px; }
  .hotline {
    position: absolute; top: 34px; right: 44px; text-align: right;
    font-family: "Archivo", sans-serif;
  }
  .hotline-label {
    font-family: "Red Hat Display", sans-serif; font-weight: 900;
    font-size: 33px; line-height: 32px; color: var(--red);
  }
  .hotline-number {
    font-style: italic; font-weight: 800; font-size: 18px; color: #111;
  }
</style>
</head>
<body>
<main class="flyer">
  <h1 class="course-title">REAL ESTATE COURSE</h1>
  <div class="headline-band"><h2 class="headline">How to Make Money In Real Estate?</h2></div>
  <p class="tagline">An investment in knowledge<br>opens up untold opportunities.</p>
  <div class="houses-art" role="img" aria-label="Rows of small white model houses with one red house in front"></div>

  <section class="sessions-box">
    <div class="sessions-art" role="img" aria-label="Illustration of a student with a laptop attending an online real estate lesson"></div>
    <p class="sessions-text">REMOTE SESSIONS<br>12 SESSION-STARTING JUNE 16</p>
  </section>

  <div class="lower-band"></div>
  <h3 class="topics-heading">Topics</h3>

  <svg width="0" height="0" style="position:absolute">
    <symbol id="tick" viewBox="0 0 14 14">
      <rect x="1" y="2" width="10" height="10" fill="none" stroke="#b08f52" stroke-width="1.2"/>
      <path d="M3.5 7 L6 9.5 L12.5 2" fill="none" stroke="#b08f52" stroke-width="1.4"/>
    </symbol>
  </svg>

  <div class="topics">
    <ul>
      <li><svg><use href="#tick"/></svg>Single-family</li>
      <li><svg><use href="#tick"/></svg>Multifamily</li>
      <li><svg><use href="#tick"/></svg>Management</li>
      <li><svg><use href="#tick"/></svg>Real Estate Concepts</li>
      <li><svg><use href="#tick"/></svg>Real Estate law</li>
    </ul>
    <ul>
      <li><svg><use href="#tick"/></svg>Investment properties</li>
      <li><svg><use href="#tick"/></svg>Foreclosures</li>
      <li><svg><use href="#tick"/></svg>Rehab</li>
      <li><svg><use href="#tick"/></svg>Foreclosures</li>
      <li><svg><use href="#tick"/></svg>Short sales</li>
    </ul>
    <ul>
      <li><svg><use href="#tick"/></svg>Development</li>
      <li><svg><use href="#tick"/></svg>Finical modeling</li>
      <li><svg><use href="#tick"/></svg>HUD properties</li>
      <li><svg><use href="#tick"/></svg>Due Diligence</li>
    </ul>
  </div>
  <div class="topics-rule"></div>

  <p class="audience">For those who have started or<br>would like to go into Real Estate.</p>

  <footer class="footer">
    <div class="address">
      <svg width="26" height="36" viewBox="0 0 26 36">
        <path d="M13 1 C6 1 2 6 2 12 C2 20 13 30 13 30 C13 30 24 20 24 12 C24 6 20 1 13 1 Z" fill="#b08f52"/>
        <circle cx="13" cy="12" r="6" fill="#fff"/>
        <ellipse cx="13" cy="33" rx="7" ry="2" fill="none" stroke="#b08f52" stroke-width="1.2"/>
      </svg>
      <span>ur address goes here,<br>street Crossroad 123</span>
    </div>
    <ul class="contacts">
      <li><svg viewBox="0 0 14 14"><path d="M3 1 L5.5 1 L6.5 4.5 L5 5.8 C6 8 7 9 9 10 L10.3 8.5 L13 9.5 L13 12 C13 12.8 12 13.5 11 13 C6 11.5 2.5 8 1 3 C0.7 2 1.5 1 3 1 Z" fill="#b08f52"/></svg>+012 - 3456 - 78901</li>
      <li><svg viewBox="0 0 14 14"><rect x="1" y="3" width="12" height="9" fill="#b08f52"/><path d="M1 3 L7 8 L13 3" fill="none" stroke="#fff" stroke-width="1"/></svg>urname@email.com</li>
      <li><svg viewBox="0 0 14 14"><circle cx="7" cy="7" r="6" fill="none" stroke="#b08f52" stroke-width="1.3"/><path d="M1 7 H13 M7 1 C4 4 4 10 7 13 C10 10 10 4 7 1" fill="none" stroke="#b08f52" stroke-width="1"/></svg>urwebsitename.com</li>
    </ul>
    <div class="hotline">
      <div class="hotline-label">HOTLINE</div>
      <div class="hotline-number">+012 - 3456 - 78901</div>
    </div>
  </footer>
</main>
</body>
</html>
```